Popcorn, ice cream, alcohol infused shakes shop

Create a clean simple website with pictures and bold type for a popcorn, ice cream and boozy shake shop. The site should have:
- Unique and Large Typography
- Large & Responsive Hero (stunning, elicits a response) Images.No concern with above or below the fold. Create a strong visual experience that encourages visitors to scroll down to read more. Use large images to visually tell a story without having to rely on just text.
- Flat image designs
- Place for me to upload an ad type video
- Hidden type menu (three line menu)
- A few small card like images (food, gift bags, tins, etc.) menu items with a brief description.

Target Market(s)

21-49 years of age for the boozy shakes. Soccer moms for sports teams & sleepovers, professionals (teachers, realtors, pharm sales), gifts for family and friends. Also some kids

Coding

Coded - Design and coding required

Number of Pages Required

5+ page

Font styles to use
Sans Serif

Colors

Designer to choose colors to be used in the design.

Requirements
Must have
• Images of gourmet popcorn, fancy shakes, ice cream, gift bags and popcorn tins. Holiday popcorn tins and gift bags along with grift certificates. Ability for visitors to send a contact form to kt@treatloft.example
• Five pages - Home Page, AboutUs, Menu, Gift/Promotion, Contact Us
Nice to have
• Smooth flow on the home page. Mostly images and bold text.
Should not have
• Too many words. Boring text fonts

```html
<!DOCTYPE html>
<html lang="en">
<head>
<meta charset="utf-8">
<title>Treat Loft</title>
<link href="https://fonts.googleapis.com/css2?family=Oswald:wght@500;600;700&family=Montserrat:wght@400;500;600;700&display=swap" rel="stylesheet">
<style>
:root{
  --ink:#24090e;
  --maroon:#3a0f17;
  --crimson:#8c0f2e;
  --wine:#5a0d1f;
  --pink:#ee1656;
  --white:#ffffff;
  --muted:#c9a9b0;
}
*{margin:0;padding:0;box-sizing:border-box}
html,body{width:1200px;height:4172px;overflow:hidden}
body{background:var(--ink);font-family:'Montserrat',sans-serif;color:var(--white);position:relative}
.display{font-family:'Oswald',sans-serif;font-weight:600;text-transform:uppercase;line-height:1}
.accent{color:var(--pink)}
.btn{display:inline-flex;align-items:center;justify-content:center;background:var(--white);color:var(--ink);font-size:14px;font-weight:500;width:170px;height:48px}
.photo{position:absolute}

/* hero */
.hero{position:absolute;left:0;top:0;width:1200px;height:860px;background:radial-gradient(circle at 70% 40%,#b4153e 0%,#7c0c27 45%,#3d0a15 100%);overflow:hidden}
.hero .photo-bg{left:0;top:0;width:1200px;height:860px;background:radial-gradient(ellipse at 50% 30%,rgba(255,230,200,.12),transparent 60%)}
.hero .photo-popcorn{left:800px;top:220px;width:400px;height:640px;background:linear-gradient(160deg,#f5e6c8 0%,#e8c88c 40%,#d8263f 70%,#b51232 100%);border-radius:200px 0 0 0;opacity:.92}
.logo{position:absolute;left:120px;top:24px;display:flex;align-items:center;gap:10px;font-weight:700;font-size:22px;color:var(--white)}
.logo .dot{width:18px;height:18px;border-radius:50%;background:var(--pink)}
.topbar{position:absolute;left:1018px;top:34px;display:flex;gap:14px}
.hero-title{position:absolute;left:128px;top:170px;font-size:112px}
.hero-title span{display:block;margin-bottom:6px}
.hero-text{position:absolute;left:128px;top:530px;width:440px;font-size:16px;line-height:1.4;color:#f3dfe3}
.hero .btn{position:absolute;left:128px;top:616px}
.pager{position:absolute;left:520px;top:784px;display:flex;align-items:center;gap:24px}
.pager .dots{display:flex;gap:8px}
.pager .dots i{width:8px;height:8px;border-radius:50%;background:#b78a93}
.pager .dots i.on{background:var(--white)}

/* deals */
.deals{position:absolute;left:0;top:860px;width:1200px;height:1340px;background:linear-gradient(180deg,#2e0b12 0%,#3b0f18 50%,#2a0a10 100%)}
.section-title{position:absolute;left:0;width:1200px;text-align:center;font-size:120px}
.section-title span{display:block;margin-bottom:8px}
.deals .section-title{top:95px}
.deals .photo-main{left:188px;top:424px;width:764px;height:676px;background:linear-gradient(150deg,#f8eed8 0%,#eccf94 35%,#f2f2f2 55%,#d31f3d 80%,#a31430 100%)}
.offer{position:absolute;left:188px;top:1115px;width:764px}
.offer p{font-size:15px;line-height:1.35;width:300px}
.price-row{display:flex;align-items:center;gap:14px;margin-top:22px}
.price{font-size:38px;font-weight:700}
.was{font-size:12px;color:var(--pink);text-decoration:line-through}
.add{display:inline-flex;align-items:center;gap:6px;background:var(--pink);color:var(--white);font-size:13px;font-weight:600;height:30px;padding:0 14px}
.arrows{position:absolute;display:flex;gap:16px}
.arrows span{width:42px;height:42px;border-radius:50%;background:var(--pink);display:flex;align-items:center;justify-content:center}
.deals .arrows{left:912px;top:1172px}

/* special */
.special{position:absolute;left:0;top:2200px;width:1200px;height:540px;background:linear-gradient(90deg,#5c0d20 0%,#9b1136 60%,#c0173f 100%);overflow:hidden}
.special .photo-sundae{left:820px;top:0;width:380px;height:540px;background:radial-gradient(ellipse at 50% 55%,#f3e4d2 0%,#c89a74 35%,#7a3a2c 65%,transparent 80%)}
.special-title{position:absolute;left:98px;top:90px;font-family:'Montserrat',sans-serif;font-weight:700;font-size:86px;line-height:1.15}
.special-text{position:absolute;left:98px;top:300px;width:480px;font-size:19px;line-height:1.35;font-weight:500}
.special .btn{position:absolute;left:98px;top:384px}

/* popular */
.popular{position:absolute;left:0;top:2740px;width:1200px;height:1010px;background:linear-gradient(180deg,#3a0d16 0%,#2c0a11 100%)}
.popular .section-title{top:110px}
.cards{position:absolute;left:98px;top:445px;display:flex;gap:22px}
.card{width:318px}
.card .photo{position:static;display:block;width:318px;height:250px}
.card .p1{background:linear-gradient(160deg,#f1d9c8,#d78a93 50%,#a3464f)}
.card .p2{background:linear-gradient(160deg,#f2a640,#9d3a1c 55%,#2b0d0a)}
.card .p3{background:linear-gradient(160deg,#f0d9b0,#d9aa6a 55%,#a87036)}
.card p{font-size:15px;line-height:1.35;margin-top:22px;width:260px}
.card .price-row{margin-top:18px;gap:10px}
.card .price{font-size:36px}
.popular .arrows{left:548px;top:885px}

/* footer */
.footer{position:absolute;left:0;top:3750px;width:1200px;height:362px;background:linear-gradient(90deg,#6a0c22 0%,#a31134 55%,#d1153f 100%)}
.footer h4{font-size:20px;font-weight:600}
.links{position:absolute;left:160px;top:70px;width:205px;text-align:right}
.links ul{list-style:none;margin-top:20px;font-size:12px;line-height:2}
.divider{position:absolute;top:0;width:1px;height:362px;background:rgba(255,255,255,.15)}
.contact{position:absolute;left:470px;top:70px;width:260px;text-align:center}
.form{margin-top:24px;display:grid;grid-template-columns:1fr 1fr;gap:10px}
.form span{display:block;height:30px;border:1px solid rgba(255,255,255,.35);font-size:11px;text-align:left;padding:8px;color:var(--muted)}
.form .msg{grid-column:1/3;height:74px}
.send{display:inline-flex;align-items:center;justify-content:center;margin-top:14px;width:132px;height:34px;background:var(--pink);font-size:13px;font-weight:600}
.follow{position:absolute;left:840px;top:70px}
.social{display:flex;gap:10px;margin-top:22px}
.social i{width:32px;height:32px;border-radius:50%;background:var(--white)}
.copy{position:absolute;left:0;top:4112px;width:1200px;height:60px;background:#1a0609;text-align:center;line-height:60px;font-size:12px;color:var(--muted)}
</style>
</head>
<body>

<header class="hero">
  <div class="photo photo-bg" role="img" aria-label="Blurred background of popcorn bowls"></div>
  <div class="photo photo-popcorn" role="img" aria-label="Striped popcorn box with popcorn spilling out"></div>
  <div class="logo"><span class="dot"></span>Treat Loft</div>
  <div class="topbar">
    <svg width="22" height="22" viewBox="0 0 22 22"><path d="M3 5h16M3 11h16M3 17h16" stroke="#fff" stroke-width="2.4"/></svg>
    <svg width="22" height="22" viewBox="0 0 22 22"><circle cx="9" cy="9" r="6" stroke="#fff" stroke-width="2.2" fill="none"/><path d="M13.5 13.5L19 19" stroke="#fff" stroke-width="2.4"/></svg>
  </div>
  <h1 class="hero-title display"><span>We Are</span><span class="accent">Food</span><span>Masters</span></h1>
  <p class="hero-text">Lorem Ipsum Is Simply Dummy Text Of The Printing And Typesetting Industry.</p>
  <a class="btn">Order Now</a>
  <div class="pager">
    <svg width="36" height="12" viewBox="0 0 36 12"><path d="M36 6H3M8 1L2 6l6 5" stroke="#fff" stroke-width="1.6" fill="none"/></svg>
    <div class="dots"><i></i><i class="on"></i><i></i></div>
    <svg width="36" height="12" viewBox="0 0 36 12"><path d="M0 6h33M28 1l6 5-6 5" stroke="#fff" stroke-width="1.6" fill="none"/></svg>
  </div>
</header>

<section class="deals">
  <h2 class="section-title display"><span>Deals and</span><span class="accent">Offers</span></h2>
  <div class="photo photo-main" role="img" aria-label="Red and white striped popcorn boxes filled with popcorn"></div>
  <div class="offer">
    <p>Save 25% on optional burger from Café Morrow</p>
    <div class="price-row"><span class="price">$87.00</span><span class="was">$99.00</span><span class="add">🛒 Add</span></div>
  </div>
  <div class="arrows">
    <span><svg width="14" height="14" viewBox="0 0 14 14"><path d="M9 2L4 7l5 5" stroke="#fff" stroke-width="2.2" fill="none"/></svg></span>
    <span><svg width="14" height="14" viewBox="0 0 14 14"><path d="M5 2l5 5-5 5" stroke="#fff" stroke-width="2.2" fill="none"/></svg></span>
  </div>
</section>

<section class="special">
  <div class="photo photo-sundae" role="img" aria-label="Ice cream sundae in a glass with cherry and chocolate sticks"></div>
  <h2 class="special-title">Today’s Special<br><span class="accent">Food</span></h2>
  <p class="special-text">Energistically negotiate stand-alone infomediaries rather than ubiquitous</p>
  <a class="btn">Shop Now</a>
</section>

<section class="popular">
  <h2 class="section-title display"><span>Most</span><span class="accent">Popular</span></h2>
  <div class="cards">
    <article class="card">
      <div class="photo p1" role="img" aria-label="Frosted pastry treats"></div>
      <p>Save 25% on optional burger from Café Morrow</p>
      <div class="price-row"><span class="price">$87.00</span><span class="was">$99.00</span><span class="add">🛒 Add</span></div>
    </article>
    <article class="card">
      <div class="photo p2" role="img" aria-label="Boozy shakes and drinks on a bar"></div>
      <p>Save 25% on optional burger from Café Morrow</p>
      <div class="price-row"><span class="price">$87.00</span><span class="was">$99.00</span><span class="add">🛒 Add</span></div>
    </article>
    <article class="card">
      <div class="photo p3" role="img" aria-label="Kraft paper gift bags"></div>
      <p>Save 25% on optional burger from Café Morrow</p>
      <div class="price-row"><span class="price">$87.00</span><span class="was">$99.00</span><span class="add">🛒 Add</span></div>
    </article>
  </div>
  <div class="arrows">
    <span><svg width="14" height="14" viewBox="0 0 14 14"><path d="M9 2L4 7l5 5" stroke="#fff" stroke-width="2.2" fill="none"/></svg></span>
    <span><svg width="14" height="14" viewBox="0 0 14 14"><path d="M5 2l5 5-5 5" stroke="#fff" stroke-width="2.2" fill="none"/></svg></span>
  </div>
</section>

<footer class="footer">
  <div class="links">
    <h4>Treat Loft</h4>
    <ul><li>Home</li><li>About Us</li><li>Menu</li><li>Gift/Promotion</li><li>Contact Us</li></ul>
  </div>
  <div class="divider" style="left:420px"></div>
  <div class="contact">
    <h4>Contact Us</h4>
    <div class="form"><span>Name</span><span>Email</span><span class="msg">Message</span></div>
    <a class="send">Send</a>
  </div>
  <div class="divider" style="left:780px"></div>
  <div class="follow">
    <h4>Follow Us</h4>
    <div class="social"><i></i><i></i><i></i></div>
  </div>
</footer>
<div class="copy">Treat Loft Copyright © 2019</div>

</body>
</html>
```